Simple and Clean business card design

We would like the design to be simple clean and to incorporate our colors.

We are open to your design and talent, we have the dots in our logo as we think of it as data points and we connect data points for people.

We are open to see the great creative and clean design you bring to the table

Contact Information for Business Card

please include: name, position, email, phone and website

Font styles to use
Sans Serif

Requirements
Must have
• my colors incorporated, simplicity
Nice to have
• lots of white space, simplicity
Should not have
• complexicity/ complex art

```html
<!DOCTYPE html>
<html lang="en">
<head>
<meta charset="utf-8">
<title>Quillorn Business Card</title>
<link rel="stylesheet" href="https://fonts.googleapis.com/css2?family=Work+Sans:wght@400;500;600&display=swap">
<style>
  :root {
    --backdrop: #161616;
    --card: #262626;
    --ink: #ffffff;
    --accent: #5b80d2;
    --muted: #e6e6e6;
  }
  * { margin: 0; padding: 0; box-sizing: border-box; }
  html, body {
    width: 1200px; height: 900px; overflow: hidden;
    background: var(--backdrop);
    font-family: "Work Sans", Arial, sans-serif;
  }
  .stage {
    width: 1200px; height: 900px;
    display: flex; flex-direction: column; align-items: center; justify-content: center;
    gap: 40px;
  }
  .card {
    position: relative;
    width: 640px; height: 366px;
    background: var(--card);
    border-bottom: 6px solid var(--accent);
    display: flex; align-items: center;
  }
  .card--front { justify-content: center; }
  .brand {
    display: flex; align-items: center; gap: 12px;
    color: var(--ink);
    font-weight: 500;
    white-space: nowrap;
    flex: none;
  }
  .brand__dot {
    width: 18px; height: 18px; border-radius: 50%;
    background: var(--accent);
    flex: none;
  }
  .card--front .brand__name { font-size: 104px; line-height: 1; }
  .card--back { padding: 0 28px 0 36px; }
  .card--back .brand__name { font-size: 54px; line-height: 1; }
  .card--back .brand__dot { width: 12px; height: 12px; }
  .divider {
    flex: none;
    width: 2px; height: 190px;
    background: var(--accent);
    margin: 0 24px 0 26px;
  }
  .contact { color: var(--muted); white-space: nowrap; }
  .contact__name {
    color: var(--accent);
    font-size: 23px; font-weight: 600;
    letter-spacing: 2px; text-transform: uppercase;
    line-height: 1.1;
  }
  .contact__role { font-size: 17px; margin-bottom: 14px; }
  .contact__address { font-size: 17px; line-height: 1.3; margin-bottom: 10px; }
  .contact__list { list-style: none; font-size: 17px; line-height: 1.35; }
  .contact__list li { display: flex; align-items: center; gap: 8px; }
  .contact__icon { width: 13px; height: 13px; flex: none; }
</style>
</head>
<body>
<main class="stage">
  <section class="card card--front">
    <div class="brand">
      <span class="brand__name">Quillorn</span>
      <span class="brand__dot"></span>
    </div>
  </section>

  <section class="card card--back">
    <div class="brand">
      <span class="brand__name">Quillorn</span>
      <span class="brand__dot"></span>
    </div>
    <div class="divider"></div>
    <div class="contact">
      <p class="contact__name">Daniel Brooks</p>
      <p class="contact__role">Founder</p>
      <p class="contact__address">4820 Linden Crest Road<br>Alder Falls, TX 75012</p>
      <ul class="contact__list">
        <li>
          <svg class="contact__icon" viewBox="0 0 16 16" aria-hidden="true"><path d="M4 1l3 3-2 2c1 2 3 4 5 5l2-2 3 3-2 3C7 15 1 9 1 3z" fill="none" stroke="#e6e6e6" stroke-width="1.4"/></svg>
          0412 386 905
        </li>
        <li>
          <svg class="contact__icon" viewBox="0 0 16 16" aria-hidden="true"><rect x="1" y="3" width="14" height="10" fill="none" stroke="#e6e6e6" stroke-width="1.4"/><path d="M1 3l7 6 7-6" fill="none" stroke="#e6e6e6" stroke-width="1.4"/></svg>
          hi@ferndata.co
        </li>
        <li>
          <svg class="contact__icon" viewBox="0 0 16 16" aria-hidden="true"><circle cx="8" cy="8" r="7" fill="none" stroke="#e6e6e6" stroke-width="1.3"/><ellipse cx="8" cy="8" rx="3" ry="7" fill="none" stroke="#e6e6e6" stroke-width="1.1"/><path d="M1 8h14" stroke="#e6e6e6" stroke-width="1.1"/></svg>
          www.ferndata.co
        </li>
      </ul>
    </div>
  </section>
</main>
</body>
</html>
```